Oil and Gas Exploration and Production company needs a business card design

We need a business card design using our logo and colors in the logo. We want a mainstream design.

```html
<!DOCTYPE html>
<html lang="en">
<head>
<meta charset="utf-8">
<title>Vesta Oil &amp; Gas — Business Card, Front and Back</title>
<link rel="stylesheet" href="https://fonts.googleapis.com/css2?family=Arimo:wght@400;700&display=swap">
<style>
  :root {
    --ink: #111111;
    --charcoal: #2a2a2a;
    --gold: #d9b53a;
    --paper: #ffffff;
    --backdrop: #e6e3de;
    --text: #1a1a1a;
  }
  * { margin: 0; padding: 0; box-sizing: border-box; }
  html, body {
    width: 1200px; height: 780px; overflow: hidden;
    background: var(--backdrop);
    font-family: "Arimo", Arial, sans-serif;
  }
  .card {
    position: absolute; top: 230px;
    width: 560px; height: 320px;
    background: var(--paper);
    overflow: hidden;
    box-shadow: 0 8px 24px rgba(0,0,0,.18);
  }
  .card--front { left: 25px; }
  .card--back { left: 615px; }
  .card-art { position: absolute; inset: 0; width: 560px; height: 320px; }

  .brand { position: absolute; display: flex; align-items: center; }
  .brand-dot { border-radius: 50%; background: var(--gold); flex: none; }
  .brand-name { font-weight: 700; color: var(--ink); white-space: nowrap; }

  .card--front .brand { left: 150px; top: 52px; gap: 10px; }
  .card--front .brand-dot { width: 20px; height: 20px; }
  .card--front .brand-name { font-size: 26px; }

  .card--back .brand { left: 0; right: 0; top: 118px; justify-content: center; gap: 14px; }
  .card--back .brand-dot { width: 30px; height: 30px; }
  .card--back .brand-name { font-size: 40px; }

  .contact { position: absolute; left: 50px; top: 148px; color: var(--text); }
  .contact-name { font-weight: 700; font-size: 19px; color: var(--ink); }
  .contact-title { font-size: 13px; color: var(--gold); margin-top: 1px; }
  .contact-lines { margin-top: 16px; font-size: 12px; line-height: 1.35; }
  .contact-line { display: flex; align-items: center; gap: 6px; }
  .contact-icon { width: 11px; height: 11px; flex: none; }

  .website {
    position: absolute; right: 25px; top: 196px;
    color: var(--paper); font-size: 13px; letter-spacing: .3px;
  }
</style>
</head>
<body>
  <main>
    <section class="card card--front" aria-label="Card front">
      <svg class="card-art" viewBox="0 0 1050 600" preserveAspectRatio="none" aria-hidden="true">
        <path d="M200 600 C 420 520, 560 420, 700 300 S 930 90, 1050 55 L 1050 80 C 930 120, 800 230, 700 330 S 460 560, 320 600 Z" fill="var(--gold)"/>
        <path d="M320 600 C 470 560, 600 450, 720 340 S 920 150, 1050 110 L 1050 600 Z" fill="var(--ink)"/>
      </svg>

      <div class="brand">
        <span class="brand-dot"></span>
        <span class="brand-name">Vesta Oil &amp; Gas</span>
      </div>

      <div class="contact">
        <div class="contact-name">Daniel Reyes</div>
        <div class="contact-title">President &amp; CEO</div>
        <div class="contact-lines">
          <div class="contact-line">PO BOX 480, Harbour Road</div>
          <div class="contact-line">5th Avenue, Leeds</div>
          <div class="contact-line">
            <svg class="contact-icon" viewBox="0 0 20 20" aria-hidden="true">
              <path d="M4 2h4l2 5-2.5 1.5a11 11 0 0 0 4 4L13 10l5 2v4a2 2 0 0 1-2 2A14 14 0 0 1 2 4a2 2 0 0 1 2-2z" fill="var(--gold)"/>
            </svg>
            (321) 555 0148
          </div>
          <div class="contact-line">
            <svg class="contact-icon" viewBox="0 0 20 20" aria-hidden="true">
              <rect x="1" y="4" width="18" height="12" fill="var(--gold)"/>
              <path d="M1 4l9 7 9-7" fill="none" stroke="var(--paper)" stroke-width="1.5"/>
            </svg>
            info@vestaenergy.com
          </div>
        </div>
      </div>

      <div class="website">www.vestaenergy.com</div>
    </section>

    <section class="card card--back" aria-label="Card back">
      <svg class="card-art" viewBox="0 0 560 320" aria-hidden="true">
        <path d="M0 238 C 55 250, 95 280, 118 320 L 0 320 Z" fill="var(--charcoal)"/>
        <path d="M0 224 C 70 236, 118 272, 140 320" fill="none" stroke="var(--gold)" stroke-width="2"/>
      </svg>

      <div class="brand">
        <span class="brand-dot"></span>
        <span class="brand-name">Vesta Oil &amp; Gas</span>
      </div>
    </section>
  </main>
</body>
</html>
```